Business Card Design (NEW FILES)

ATTENTION: New vector files are available. Please update your design to reflect/use the new (better resolution) logo images.

Seeking a unique and professional business card design for a commercial drone photography/videography business. The layout should feature
the logo (attached) and include the following information:
Owen Tarrick
614-502-7738
www.skylarkreelworks.example
NRD Certified Remote Pilot

Owen Tarrick

```html
<!DOCTYPE html>
<html lang="en">
<head>
<meta charset="utf-8">
<title>Skylark Reelworks – Business Card</title>
<link rel="stylesheet" href="https://fonts.googleapis.com/css2?family=Montserrat:wght@800&family=Open+Sans:wght@400;600&display=swap">
<style>
  :root {
    --backdrop: #232323;
    --orange: #ec8b56;
    --orange-deep: #e27840;
    --orange-light: #f6b47f;
    --navy: #1b1b4b;
    --teal: #17b3b6;
    --white: #ffffff;
  }
  * { box-sizing: border-box; margin: 0; padding: 0; }
  html, body {
    width: 1200px; height: 780px; overflow: hidden;
    background: var(--backdrop);
    font-family: "Open Sans", Arial, sans-serif;
  }
  .stage {
    width: 1200px; height: 780px;
    display: flex; align-items: center; justify-content: center; gap: 40px;
  }
  .card {
    position: relative;
    width: 540px; height: 309px;
    border-radius: 22px;
    overflow: hidden;
    box-shadow: 0 14px 30px rgba(0,0,0,.55);
  }
  /* Front */
  .card-front { background: var(--orange); }
  .drone-artwork {
    position: absolute; left: 60px; top: 20px; width: 430px; height: 250px;
    border-radius: 50%;
    background: radial-gradient(ellipse at 55% 45%, var(--orange-light) 0%, var(--orange) 55%, var(--orange-deep) 100%);
    opacity: .75;
  }
  .brand {
    position: absolute;
    display: flex; align-items: center; gap: 8px;
    color: var(--navy);
    font-family: "Open Sans", Arial, sans-serif;
    font-weight: 600;
    letter-spacing: .04em;
    white-space: nowrap;
  }
  .brand-dot {
    width: 14px; height: 14px; border-radius: 50%;
    background: var(--navy);
  }
  .card-front .brand { left: 60px; bottom: 48px; font-size: 20px; }
  /* Back */
  .card-back { background: var(--white); }
  .card-back .waves { position: absolute; inset: 0; width: 100%; height: 100%; }
  .card-back .brand { left: 36px; top: 40px; font-size: 17px; }
  .contact {
    position: absolute; right: 30px; top: 78px;
    text-align: right; color: var(--white);
  }
  .person-name {
    font-family: "Montserrat", Arial, sans-serif;
    font-weight: 800; font-size: 29px; line-height: 1;
    white-space: nowrap;
  }
  .person-name .first { color: var(--orange); }
  .role { font-size: 13px; margin-top: 3px; }
  .credentials { font-size: 13px; line-height: 1.4; margin-top: 22px; }
  .details { list-style: none; margin-top: 14px; font-size: 13px; line-height: 1.6; }
  .details li { display: flex; align-items: center; justify-content: flex-end; gap: 8px; white-space: nowrap; }
  .details svg { width: 12px; height: 12px; fill: none; stroke: var(--orange); stroke-width: 2; }
</style>
</head>
<body>
<main class="stage">
  <section class="card card-front">
    <div class="drone-artwork" role="img" aria-label="Embossed drone illustration with camera aperture, tone on tone in orange"></div>
    <div class="brand"><span class="brand-dot"></span>SKYLARK REELWORKS</div>
  </section>

  <section class="card card-back">
    <svg class="waves" viewBox="0 0 540 309" preserveAspectRatio="none" aria-hidden="true">
      <path class="wave-orange" d="M370 0 C305 12 272 58 248 106 C210 188 120 245 0 262 L0 272 C132 253 222 192 262 108 C287 60 320 12 385 0 Z" fill="var(--orange)"/>
      <path class="wave-teal" d="M255 128 C215 202 130 258 0 278 L0 284 C140 264 228 208 266 136 Z" fill="var(--teal)"/>
      <path class="wave-navy" d="M400 0 C335 10 300 60 275 110 C235 195 145 262 0 288 L0 309 L540 309 L540 0 Z" fill="var(--navy)"/>
    </svg>
    <div class="brand"><span class="brand-dot"></span>SKYLARK REELWORKS</div>
    <div class="contact">
      <h1 class="person-name"><span class="first">Owen</span> Tarrick</h1>
      <p class="role">Owner</p>
      <p class="credentials">NRD Certified Remote Pilot<br>Fully Insured</p>
      <ul class="details">
        <li>614-502-7738
          <svg viewBox="0 0 24 24" aria-hidden="true"><path d="M5 3h4l2 5-3 2a12 12 0 0 0 6 6l2-3 5 2v4a2 2 0 0 1-2 2A18 18 0 0 1 3 5a2 2 0 0 1 2-2z"/></svg>
        </li>
        <li>www.skylarkreelworks.example
          <svg viewBox="0 0 24 24" aria-hidden="true"><circle cx="12" cy="12" r="10"/><path d="M2 12h20M12 2a15 15 0 0 1 0 20M12 2a15 15 0 0 0 0 20"/></svg>
        </li>
      </ul>
    </div>
  </section>
</main>
</body>
</html>
```